Business Card Design

New business card design

Target Market(s)

Residential & Commercial Property Managers

Industry/Entity Type

Plumbing Services

Contact Information for Business Card

Name - Rowan Keddle, title - Director, Phone Number - 0431 286 517, email - rowan@tbk-plumbing.com.au, Company ABN - 73 215 904 386,

Font styles to use
Sans Serif

Colors
0054AA
0677BA
7BADD7
CADEEF
E8F1F8

```html
<!DOCTYPE html>
<html lang="en">
<head>
<meta charset="utf-8">
<title>TBK Plumbing Services – Business Card</title>
<link rel="stylesheet" href="https://fonts.googleapis.com/css2?family=Montserrat:wght@400;500;700&display=swap">
<style>
  :root {
    --page-bg: #e6e8eb;
    --card-dark: #1f242b;
    --card-dark-gloss: #2a3038;
    --card-light: #ffffff;
    --ink: #1f242b;
    --ink-on-dark: #151a1f;
    --accent: #29a6e0;
    --on-dark: #ffffff;
  }
  * { box-sizing: border-box; margin: 0; padding: 0; }
  html, body {
    width: 1200px; height: 912px; overflow: hidden;
    background: var(--page-bg);
    font-family: "Montserrat", sans-serif;
  }
  .canvas { position: relative; width: 1200px; height: 912px; }
  .card {
    position: absolute; width: 620px; height: 378px;
    border-radius: 18px; overflow: hidden;
    box-shadow: 0 10px 28px rgba(0,0,0,0.18);
  }
  .card--back {
    left: 290px; top: 50px;
    background: linear-gradient(115deg, var(--card-dark) 0%, var(--card-dark) 55%, var(--card-dark-gloss) 70%, var(--card-dark) 85%);
  }
  .card--front {
    left: 290px; top: 480px;
    background: var(--card-light);
  }
  .company-name {
    position: absolute; left: 0; right: 0;
    text-align: center; white-space: nowrap;
    font-weight: 500; font-size: 34px; line-height: 1;
  }
  .card--back .company-name { top: 172px; color: var(--ink-on-dark); }
  .card--front .company-name { top: 86px; color: var(--ink); }

  .contact-band {
    position: absolute; left: 0; right: 0; bottom: 0; height: 160px;
    background: var(--card-dark);
    display: flex; align-items: center; justify-content: center;
    gap: 22px; padding: 0 24px;
  }
  .person { text-align: right; white-space: nowrap; }
  .person__name {
    color: var(--accent); font-weight: 700; font-size: 31px; line-height: 1.1;
  }
  .person__title {
    color: var(--on-dark); font-weight: 400; font-size: 19px; margin-top: 2px;
  }
  .divider { width: 1px; height: 88px; background: var(--accent); flex: none; }
  .details {
    list-style: none; color: var(--on-dark);
    font-size: 15px; font-weight: 400; white-space: nowrap;
  }
  .details li { display: flex; align-items: center; gap: 7px; line-height: 1.75; }
  .details__label { color: var(--accent); }
  .details svg { width: 15px; height: 15px; flex: none; }
</style>
</head>
<body>
<main class="canvas">
  <section class="card card--back" aria-label="Business card back">
    <div class="company-name">TBK Plumbing Services</div>
  </section>

  <section class="card card--front" aria-label="Business card front">
    <div class="company-name">TBK Plumbing Services</div>
    <div class="contact-band">
      <div class="person">
        <div class="person__name">Rowan Keddle</div>
        <div class="person__title">Director</div>
      </div>
      <div class="divider"></div>
      <ul class="details">
        <li><span class="details__label">ABN</span> - 73 215 904 386</li>
        <li>
          <svg viewBox="0 0 16 16" aria-hidden="true"><path fill="#29a6e0" d="M3.6 1.5l2.2 2.6-1.3 1.6c.9 2 2.5 3.6 4.5 4.6l1.6-1.3 2.7 2.2-1.3 2.3C7 13 2.9 8.9 1.5 3l2.1-1.5z"/></svg>
          0431 286 517
        </li>
        <li>
          <svg viewBox="0 0 16 16" aria-hidden="true"><rect x="1" y="3.5" width="14" height="9" fill="#29a6e0"/><path d="M1.5 4l6.5 5 6.5-5" fill="none" stroke="#1f242b" stroke-width="1.2"/></svg>
          rowan@tbk-plumbing.com.au
        </li>
      </ul>
    </div>
  </section>
</main>
</body>
</html>
```